Bright Harbor website redesign

We need a redesign for a website: mybrightharbor.example.

I already created a video going over what exactly is needed in the design.

See Video here: https://files.example.net/file/d/7xQpL2mR9vTz4KwB8nYcH3jDs6FgA1eU0/view?usp=sharing

plain badge Slide shown in Video: https://slides.example.net/presentation/d/9KP_Rtnwq3XbzmLeYc7VhJ2GoUd4Fs_PaiTe6q1kQ5Wr/edit?usp=sharing

Holidays in India so we did not get enough design entries or quality.

Target Market(s)

Dentistry

Industry/Entity Type

Dentistry

Number of Pages Required

1 page

Colors
0094D4
00A9DD
6FCCEA
C7EBF8
E9F6FB
00AB8E
00BBA5
67D7C9
C6EFE9
E9F9F6

Requirements
Must have
• See 13 min video link in description - shows what to do.

```html
<!DOCTYPE html>
<html lang="en">
<head>
<meta charset="utf-8">
<title>Bright Harbor — Dental Care</title>
<link rel="stylesheet" href="https://fonts.googleapis.com/css2?family=Montserrat:wght@300;400;600;700&family=Open+Sans:wght@400;600;700&display=swap">
<style>
:root{
  --blue:#2196e3;
  --blue-deep:#0b7fd0;
  --blue-light:#3aa6f0;
  --green:#6ab42d;
  --red:#e11b22;
  --ink:#333a3f;
  --title:#2b4656;
  --muted:#cfd8cf;
  --grey-bg:#f4f4f4;
  --ice:#eaf5fb;
  --star:#f5b820;
  --white:#ffffff;
}
*{box-sizing:border-box;margin:0;padding:0}
html,body{width:1200px;height:4231px;overflow:hidden}
body{font-family:"Open Sans",sans-serif;color:var(--ink);background:var(--white);position:relative}
.abs{position:absolute}
.title{font-family:"Montserrat",sans-serif;font-weight:300;color:var(--title);letter-spacing:1px;text-transform:uppercase}
.title b{font-weight:700}
.rule{height:3px;width:50px;background:var(--green);position:absolute}
.btn{position:absolute;border-radius:30px;color:#fff;font-family:"Montserrat",sans-serif;font-weight:700;font-size:12px;display:flex;align-items:center;justify-content:center;letter-spacing:.3px}
.btn-green{background:var(--green)}
.btn-red{background:var(--red)}

/* header */
.site-header{position:absolute;left:0;top:0;width:1200px;height:105px;background:#fff}
.brand{left:92px;top:22px;font-family:"Montserrat",sans-serif;font-weight:600;font-size:30px;color:var(--green)}
.brand-dot{display:inline-block;width:14px;height:14px;border-radius:50%;background:var(--red);margin-left:6px;vertical-align:middle}
.phone{left:640px;top:15px;font-size:15px;font-weight:600;color:var(--ink);display:flex;align-items:center;gap:8px}
.nav{left:316px;top:68px;display:flex;gap:0;font-size:13px;color:#444}
.nav span{margin-right:36px}
.nav .active{position:relative}
.nav .active:after{content:"";position:absolute;left:0;right:-8px;top:29px;height:4px;background:var(--green)}

/* hero */
.hero{position:absolute;left:0;top:105px;width:1200px;height:570px;background:linear-gradient(180deg,#3aa3f2 0%,#1f8fe6 60%,#1b7ed8 100%)}
.hero-art{position:absolute;left:560px;top:100px;width:640px;height:420px;border-radius:40px;background:radial-gradient(ellipse at 50% 45%,rgba(255,255,255,.55),rgba(255,255,255,.12) 55%,rgba(255,255,255,0) 75%)}
.hero h1{position:absolute;left:107px;top:162px;font-family:"Montserrat",sans-serif;color:#fff;font-size:38px;line-height:46px;font-weight:300;letter-spacing:1px}
.hero h1 b{font-weight:700}
.hero p{position:absolute;left:109px;top:264px;color:#fff;font-family:"Montserrat",sans-serif;font-weight:600;font-size:17px;line-height:23px;letter-spacing:1.2px}

/* team */
.team{position:absolute;left:0;top:675px;width:1200px;height:586px;background:var(--grey-bg)}
.team .title{position:absolute;width:1200px;text-align:center;top:64px;font-size:30px}
.portrait{position:absolute;top:174px;width:258px;height:258px;background:linear-gradient(180deg,#e9e9e9,#d7d7d7);box-shadow:0 2px 10px rgba(0,0,0,.08)}
.portrait.on{background:linear-gradient(180deg,#eef0f2,#c9cdd2 70%,#2b2f36 100%)}
.member{position:absolute;top:460px;width:300px;text-align:center}
.member h3{font-family:"Open Sans",sans-serif;font-size:18px;font-weight:600;color:#d6d6d6}
.member p{font-size:15px;color:#cfe5b9;margin-top:6px}
.member.on h3{color:var(--ink)}
.member.on p{color:var(--green)}
.arrow{position:absolute;top:302px}

/* bio */
.bio{position:absolute;left:170px;top:1345px;width:860px;text-align:center;font-size:14.5px;line-height:27px;color:#3a3a3a}
.bio p+p{margin-top:16px}
.assoc{position:absolute;top:1530px;left:187px;display:flex;gap:6px}
.assoc div{width:205px;height:78px;border:2px solid #cfd9e2;border-radius:3px;display:flex;align-items:center;justify-content:center;text-align:center;font-size:13px;line-height:19px;color:#3a3a3a;padding:0 10px}

/* services */
.services{position:absolute;left:0;top:1719px;width:1200px;height:937px;background:var(--ice)}
.services .title{position:absolute;width:1200px;text-align:center;top:46px;font-size:30px}
.svc{position:absolute;width:222px;height:222px;border-radius:50%;background:#fff;box-shadow:0 4px 16px rgba(33,150,227,.10);display:flex;flex-direction:column;align-items:center;justify-content:center;gap:14px;text-align:center;font-family:"Montserrat",sans-serif;font-weight:700;font-size:14px;color:var(--title);line-height:18px}
.svc.on{background:var(--blue);color:#fff}
.svc.on .ico{background:rgba(255,255,255,.2);border-radius:50%;padding:10px}

/* difference */
.diff .title{position:absolute;left:153px;top:2753px;font-size:26px;line-height:30px}
.diff-copy{position:absolute;left:153px;top:2860px;width:566px;font-size:12.3px;line-height:17px;color:#555}
.diff-copy p+p{margin-top:17px}
.rating{position:absolute;left:770px;top:2728px;width:304px;height:440px;background:#f2f2f2}
.rating h4{position:absolute;width:304px;top:20px;text-align:center;font-size:14px;font-weight:700;color:#333;letter-spacing:.5px}
.stars{color:var(--star);letter-spacing:3px}
.badge{position:absolute;height:32px;border-radius:3px}
.review{position:absolute;left:52px;top:165px;width:214px;height:247px;background:#fff;box-shadow:0 1px 6px rgba(0,0,0,.1);font-size:9px;line-height:11px;color:#444}

/* cta */
.cta{position:absolute;left:0;top:3267px;width:1200px;height:471px;background:linear-gradient(90deg,#1f95e6 0%,#1d8ad9 60%,#1679c6 100%)}
.cta-photo{position:absolute;left:135px;top:72px;width:435px;height:312px;border-radius:0 90px 0 90px;background:linear-gradient(135deg,#6c8aa0,#cbd6de 45%,#e9eef2 70%,#9fb3c4)}
.cta h2{position:absolute;left:624px;top:122px;color:#fff;font-family:"Montserrat",sans-serif;font-size:27px;line-height:36px;font-weight:300;letter-spacing:1.2px}
.cta h2 b{font-weight:700}
.cta .sub{position:absolute;left:627px;top:222px;color:#fff;font-size:19px;letter-spacing:.4px}

/* footer */
.foot h5{position:absolute;top:3796px;font-family:"Montserrat",sans-serif;font-size:17px;font-weight:700;color:var(--title);letter-spacing:.6px}
.foot .rule{top:3826px;width:36px;height:2px;background:var(--blue)}
.foot-line{position:absolute;left:128px;font-size:13px;color:#444;display:flex;gap:12px;align-items:flex-start;line-height:20px}
.hours{position:absolute;left:460px;top:3856px;font-size:13px;color:#444}
.hours div{display:flex;height:29.5px}
.hours span:first-child{width:115px}
.map{position:absolute;left:753px;top:3853px;width:307px;height:182px;border:1px solid #ccc;background:linear-gradient(135deg,#f4f4f2,#e9ece8 60%,#f3efe2)}
.bottom{position:absolute;left:0;top:4096px;width:1200px;height:135px;border-top:1px solid #e3e3e3}
.bottom-links{position:absolute;left:131px;top:28px;display:flex;font-size:12px;color:#333}
.bottom-links span{margin-right:38px}
.copy{position:absolute;left:131px;top:62px;font-size:11px;color:#444}
.social{position:absolute;left:923px;top:26px;display:flex;gap:5px}
.social i{width:25px;height:25px;border-radius:50%;background:var(--green);display:block}
</style>
</head>
<body>

<header class="site-header">
  <div class="abs brand">Bright Harbor<span class="brand-dot"></span></div>
  <div class="abs phone">
    <svg width="20" height="20" viewBox="0 0 20 20"><circle cx="10" cy="10" r="10" fill="#e11b22"/><path d="M7 5.5l2 2-1 1.3c.6 1.3 1.6 2.3 2.9 2.9l1.3-1 2 2-1.2 1.6C9.7 14 6 10.3 5.7 6.7z" fill="#fff"/></svg>
    (555) 014-2290
  </div>
  <div class="btn btn-green" style="left:815px;top:7px;width:146px;height:36px;font-size:12px">Schedule Online</div>
  <div class="btn" style="left:966px;top:7px;width:145px;height:36px;background:var(--blue-light);font-size:12px">Emergency</div>
  <nav class="abs nav">
    <span class="active">About Us ▾</span><span>Services ▾</span><span>Financing</span><span>Testimonials</span><span>New Patient Visit</span><span>Specials</span><span>Contact Us</span><span>Blog</span>
  </nav>
</header>

<section class="hero">
  <div class="hero-art" role="img" aria-label="Tooth model with dental floss, mirror and toothbrush on a blue surface"></div>
  <h1>CREATING<br><b>HEALTHIER SMILES</b></h1>
  <p>WITH ADVANCED TECHNOLOGY AND<br>AFFORDABLE TREATMENT</p>
  <div class="btn btn-green" style="left:103px;top:332px;width:233px;height:51px;font-size:13px">BOOK AN APPOINTMENT</div>
</section>

<section class="team">
  <h2 class="title">Meet <b>Our Team</b></h2>
  <div class="rule" style="left:554px;top:115px;width:50px;height:2px"></div>
  <svg class="arrow" style="left:55px" width="26" height="38" viewBox="0 0 26 38"><path d="M20 3L5 19l15 16" fill="none" stroke="#777" stroke-width="4"/></svg>
  <svg class="arrow" style="left:1118px" width="26" height="38" viewBox="0 0 26 38"><path d="M6 3l15 16L6 35" fill="none" stroke="#777" stroke-width="4"/></svg>
  <div class="portrait" style="left:171px" role="img" aria-label="Portrait of Dr. Arun Mehta"></div>
  <div class="portrait on" style="left:476px" role="img" aria-label="Portrait of Dr. Leena Varma"></div>
  <div class="portrait" style="left:778px" role="img" aria-label="Portrait of Dr. Nisha Rao"></div>
  <div class="member" style="left:162px"><h3>Meet Dr. Arun Mehta</h3><p>General Dentist</p></div>
  <div class="member on" style="left:455px"><h3>Dr. Leena Varma</h3><p>Endodontist</p></div>
  <div class="member" style="left:758px"><h3>Dr. Nisha Rao</h3><p>Cosmetic Dentist</p></div>
</section>

<section class="bio">
  <p>Dr. Varma received her specialty training in Endodontics from Westbrook University. She graduated with a Master of Science in dentistry degree, in endodontics. She has practiced in Southern California for many years as a general dentist before specializing in endodontics and uses her experience to help her patients make the right decisions, regarding their treatment plans. She is gentle, compassionate and is committed to providing the optimum care for her patients.</p>
  <p>Dr. Varma is a member of several professional and service organizations, including:</p>
</section>
<div class="assoc">
  <div>Continental Dental Society (CDS)</div>
  <div>State Dental Council (SDC)</div>
  <div>Heritage Dental Guild (HDG)</div>
  <div>Harbor County Dental Circle (HCDC)</div>
</div>

<section class="services">
  <h2 class="title">Our <b>Services</b></h2>
  <div class="rule" style="left:567px;top:96px;width:70px;height:2px"></div>
</section>
<svg width="0" height="0" style="position:absolute">
  <defs>
    <symbol id="tooth" viewBox="0 0 40 40"><path d="M12 6c3 0 5 2 8 2s5-2 8-2c5 0 8 4 7 10-1 5-3 7-4 12-1 4-2 8-4 8s-2-5-3-9c-1-3-2-4-4-4s-3 1-4 4c-1 4-1 9-3 9s-3-4-4-8c-1-5-3-7-4-12-1-6 2-10 7-10z" fill="none" stroke="currentColor" stroke-width="2" stroke-linejoin="round"/></symbol>
  </defs>
</svg>
<div class="svc on" style="left:137px;top:1847px"><svg class="ico" width="64" height="64" style="color:#fff"><use href="#tooth"/></svg>DENTAL IMPLANTS</div>
<div class="svc" style="left:372px;top:1847px"><svg width="44" height="44" style="color:var(--blue)"><use href="#tooth"/></svg>COSMETIC<br>DENTISTRY</div>
<div class="svc" style="left:606px;top:1847px"><svg width="44" height="44" style="color:var(--blue)"><use href="#tooth"/></svg>BRACES</div>
<div class="svc" style="left:846px;top:1847px"><svg width="44" height="44" style="color:var(--blue)"><use href="#tooth"/></svg>CROWNS</div>
<div class="svc" style="left:148px;top:2094px"><svg width="44" height="44" style="color:var(--blue)"><use href="#tooth"/></svg>BRIDGE</div>
<div class="svc" style="left:383px;top:2094px"><svg width="44" height="44" style="color:var(--blue)"><use href="#tooth"/></svg>EXTRACTIONS</div>
<div class="svc" style="left:618px;top:2094px"><svg width="44" height="44" style="color:var(--blue)"><use href="#tooth"/></svg>GUM DISEASE</div>
<div class="svc" style="left:854px;top:2094px"><svg width="44" height="44" style="color:var(--blue)"><use href="#tooth"/></svg>ROOT CANAL</div>
<div class="svc" style="left:148px;top:2342px"><svg width="44" height="44" style="color:var(--blue)"><use href="#tooth"/></svg>DENTURES</div>
<div class="svc" style="left:383px;top:2342px"><svg width="44" height="44" style="color:var(--blue)"><use href="#tooth"/></svg>EMERGENCY<br>DENTISTRY</div>
<div class="svc" style="left:618px;top:2342px"><svg width="44" height="44" style="color:var(--blue)"><use href="#tooth"/></svg>VENEERS</div>
<div class="svc" style="left:854px;top:2342px"><svg width="44" height="44" style="color:var(--blue)"><use href="#tooth"/></svg>CLEARPATH<br>ALIGNERS</div>

<section class="diff">
  <h2 class="title">Experience the Bright<br><b>Harbor Difference</b></h2>
  <div class="rule" style="left:153px;top:2830px;width:70px;height:2px"></div>
  <div class="diff-copy">
    <p>Your smile is our #1 priority. At Bright Harbor, we provide affordable and expert dental solutions. Whether you are looking for a family dentist or have any emergency such as needing a root canal in Lakemont, we are here for you! We want to keep your teeth healthy inside and out. We don't just clean teeth and send you on your way, we want to get to know you.</p>
    <p>We accept most HMO and PPO insurances. We offer various financing options through SmilePay Credit, Lendwell Club and In-House Plans.</p>
    <p>To constantly strive to achieve the highest level of skills and modern techniques and equipment so we can provide our patients with the best that Dentistry has to offer at our dental office in Lakemont, Harbor County, CA.</p>
    <p>We provide patients with the best experience you can find in all of Southern California. We provide a comfortable and friendly atmosphere to shatter any fears you may have. We supply you with all the information on your dental health options so you can feel comfortable in the choices you make, whether it's a routine check-up or dental implants in Lakemont.</p>
    <p>We are available for Emergency and Walk-ins.</p>
  </div>
  <aside class="rating">
    <h4>AVERAGE RATING</h4>
    <div class="abs" style="left:90px;top:42px;font-size:17px"><span class="stars">★★★★★</span> <b style="font-size:14px;color:#333">4.9</b></div>
    <div class="abs" style="left:112px;top:75px;font-size:11px;color:#555;display:flex;gap:6px;align-items:center"><i style="width:16px;height:16px;border-radius:50%;background:var(--blue);display:block"></i>126 Reviews</div>
    <div class="abs" style="left:62px;top:108px;width:194px;height:42px;background:#fff;border-radius:3px"></div>
    <div class="badge" style="left:70px;top:113px;width:55px;background:#eef3fb"></div>
    <div class="badge" style="left:132px;top:113px;width:55px;background:#fdeceb"></div>
    <div class="badge" style="left:194px;top:113px;width:55px;background:#3b5b98"></div>
    <svg class="abs" style="left:30px;top:280px" width="12" height="18" viewBox="0 0 12 18"><path d="M10 2L3 9l7 7" fill="none" stroke="#2196e3" stroke-width="2.5"/></svg>
    <svg class="abs" style="left:262px;top:280px" width="12" height="18" viewBox="0 0 12 18"><path d="M2 2l7 7-7 7" fill="none" stroke="#2196e3" stroke-width="2.5"/></svg>
    <div class="review">
      <div class="abs" role="img" aria-label="Reviewer avatar" style="left:14px;top:14px;width:36px;height:36px;border-radius:50%;background:linear-gradient(135deg,#b08770,#6b4a3a)"></div>
      <div class="abs stars" style="left:76px;top:12px;font-size:13px">★★★★★</div>
      <div class="abs" style="left:76px;top:34px;font-size:13px;font-weight:700;color:#333">Dana Whitfield</div>
      <div class="abs" style="left:14px;top:68px;width:186px">Dr. Varma and her staff are awesome! Everyone is so nice and pleasant. I always have a great experience! I don't ever feel rushed and time is taken to answer questions and make sure we are on the same page! This office i... <span style="color:var(--blue)">more</span></div>
      <div class="abs" style="left:14px;top:158px;color:#888">26 February, 2021</div>
      <div class="abs" style="left:0;top:185px;width:214px;height:1px;background:#eee"></div>
      <div class="abs" style="left:14px;top:211px;font-size:9px">Source:</div>
      <div class="abs" style="left:128px;top:202px;width:72px;height:26px;border-radius:3px;background:#eef3fb"></div>
    </div>
  </aside>
</section>

<section class="cta">
  <div class="cta-photo" role="img" aria-label="Dentist examining a smiling patient in the dental chair"></div>
  <h2><b>COMMITTED TO EXCELLENCE</b><br>IN ORAL HEALTH CARE</h2>
  <div class="abs" style="left:627px;top:199px;width:40px;height:3px;background:#fff"></div>
  <div class="abs" style="left:627px;top:206px;width:26px;height:3px;background:#fff"></div>
  <p class="sub">Free Exam and X-Rays for New Patients</p>
  <div class="btn btn-green" style="left:620px;top:274px;width:227px;height:48px;font-size:12px">BOOK AN APPOINTMENT</div>
</section>

<footer class="foot">
  <h5 style="left:128px">BRIGHT HARBOR</h5><div class="rule" style="left:128px"></div>
  <h5 style="left:460px">OFFICE HOURS</h5><div class="rule" style="left:460px"></div>
  <h5 style="left:749px">OUR LOCATION</h5><div class="rule" style="left:749px"></div>
  <div class="foot-line" style="top:3856px">
    <svg width="16" height="22" viewBox="0 0 16 22"><path d="M8 1a7 7 0 0 0-7 7c0 5 7 13 7 13s7-8 7-13a7 7 0 0 0-7-7z" fill="#2b4656"/><circle cx="8" cy="8" r="2.6" fill="#fff"/></svg>
    <span>48 Harbor Light Ave., Suite A<br>Lakemont, CA 90017</span>
  </div>
  <div class="foot-line" style="top:3920px">
    <svg width="16" height="16" viewBox="0 0 16 16"><path d="M3 1l3 3-1.5 2c1 2 2.5 3.5 4.5 4.5L11 9l3 3-2 2.5C6.5 14 2 9.5 1.5 3z" fill="#2b4656"/></svg>
    <span>Call Us: (555) 014-2290</span>
  </div>
  <div class="foot-line" style="top:3950px">
    <svg width="16" height="16" viewBox="0 0 16 16"><rect x="1" y="3" width="14" height="10" fill="#2b4656"/><path d="M1 3l7 6 7-6" fill="none" stroke="#fff" stroke-width="1.3"/></svg>
    <span>hello@mybrightharbor.example</span>
  </div>
  <div class="btn btn-red" style="left:128px;top:3999px;width:207px;height:36px;font-size:12px">BOOK AN APPOINTMENT</div>
  <div class="hours">
    <div><span>Monday:</span><span>10AM–7PM</span></div>
    <div><span>Tuesday:</span><span>10AM–7PM</span></div>
    <div><span>Wednesday:</span><span>9AM–6PM</span></div>
    <div><span>Thursday:</span><span>9AM–6PM</span></div>
    <div><span>Friday:</span><span>9AM–5PM</span></div>
    <div><span>Saturday:</span><span>9AM–1PM</span></div>
  </div>
  <div class="map" role="img" aria-label="Street map showing the office location"></div>
  <div class="bottom">
    <div class="bottom-links"><span>About Us</span><span>Services</span><span>Financing</span><span>Testimonials</span><span>New Patient Visit</span><span>Specials</span><span>Contact Us</span><span>Blog</span></div>
    <div class="copy">2021 Bright Harbor &nbsp;|&nbsp; All Rights Reserved</div>
    <div class="social"><i></i><i></i><i></i><i></i><i></i></div>
  </div>
</footer>

</body>
</html>
```